Vantro cards

I am in the auto motive, transportation business I would like a business card that is Something cool, modern edgy, having to do with car culture. I offer towing service for high and exotic cars. I also provide towing for collisions and car accidents. I offer open and enclosed transport nationwide.

Target Market(s)

Car culture people high end auto collectors

Industry/Entity Type

Towing car carrier

Contact Information for Business Card

My company colors black yellow and silver

Font styles to use
Serif

```html
<!DOCTYPE html>
<html lang="en">
<head>
<meta charset="utf-8">
<title>Vantro cards</title>
<link rel="stylesheet" href="https://fonts.googleapis.com/css2?family=Arvo:wght@400;700&display=swap">
<style>
  :root {
    --yellow: #fbe05c;
    --black: #0b0b0b;
    --white: #ffffff;
    --silver: #9a9a9a;
    --backdrop: #b4b4b4;
  }
  * { box-sizing: border-box; margin: 0; padding: 0; }
  html, body { width: 1200px; height: 1200px; overflow: hidden; }
  body {
    background: var(--backdrop);
    font-family: "Arvo", Georgia, serif;
    color: var(--black);
    position: relative;
  }
  .card {
    position: absolute;
    top: 303px;
    height: 593px;
    overflow: hidden;
  }
  .card-front { left: 201px; width: 369px; background: var(--yellow); }
  .card-back { left: 599px; width: 364px; background: var(--yellow); }

  .brand-name {
    position: absolute;
    left: 0; right: 0;
    text-align: center;
    font-weight: 700;
    font-size: 50px;
    letter-spacing: 2px;
    color: var(--black);
  }
  .card-front .brand-name { top: 150px; }
  .card-back .brand-name { top: 155px; }

  .vehicle-art {
    position: absolute;
    left: 0; right: 0;
    top: 335px;
    height: 150px;
    background: linear-gradient(180deg, var(--yellow) 0%, #8a7b33 55%, var(--black) 100%);
  }
  .front-footer {
    position: absolute;
    left: 0; right: 0; bottom: 0;
    top: 485px;
    background: var(--black);
  }
  .front-web {
    position: absolute;
    left: 0; right: 0;
    top: 538px;
    text-align: center;
    color: var(--yellow);
    font-size: 15px;
  }

  .back-top { position: absolute; left: 0; top: 0; width: 364px; height: 340px; }
  .contact { position: absolute; left: 0; right: 0; text-align: center; }
  .person-name { top: 346px; font-weight: 700; font-size: 24px; letter-spacing: 0.5px; }
  .person-role { top: 377px; font-size: 15px; }
  .icon-row {
    position: absolute; top: 404px; left: 0; right: 0;
    display: flex; justify-content: center; align-items: center; gap: 4px;
  }
  .icon-row .rule { width: 52px; height: 1px; background: #5a5a3a; margin: 0 4px; }
  .icon {
    width: 25px; height: 25px; border-radius: 3px; background: var(--black);
    display: flex; align-items: center; justify-content: center;
  }
  .contact-line { font-size: 15px; line-height: 21px; }
  .phone { top: 436px; }
  .email { top: 457px; }
  .web { top: 477px; }
  .divider { position: absolute; top: 507px; left: 88px; width: 195px; height: 1px; background: #6b6642; }
  .address { top: 528px; font-size: 15px; line-height: 21px; }
</style>
</head>
<body>
  <section class="card card-front">
    <div class="brand-name">VANTRO</div>
    <div class="vehicle-art" role="img" aria-label="Black silhouette of a flatbed tow truck"></div>
    <div class="front-footer"></div>
    <p class="front-web">www.vantrotow.com</p>
  </section>

  <section class="card card-back">
    <svg class="back-top" viewBox="0 0 364 340" aria-hidden="true">
      <polygon points="0,0 364,0 364,313 233,313 182,334 130,313 0,313" fill="var(--white)"/>
    </svg>
    <div class="brand-name">VANTRO</div>

    <p class="contact person-name">MARCUS HALE</p>
    <p class="contact person-role">Managing Director</p>

    <div class="icon-row">
      <span class="rule"></span>
      <span class="icon">
        <svg width="17" height="17" viewBox="0 0 24 24" aria-hidden="true"><path fill="#fbe05c" d="M3 8c0-2 3-3 9-3s9 1 9 3v2h-5V8.5c-1-.4-2.5-.5-4-.5s-3 .1-4 .5V10H3zM6 12h12l2 8H4zm6 2.2a2.3 2.3 0 1 0 0 4.6 2.3 2.3 0 0 0 0-4.6z"/></svg>
      </span>
      <span class="icon">
        <svg width="17" height="17" viewBox="0 0 24 24" aria-hidden="true"><rect x="3" y="6" width="18" height="12" fill="none" stroke="#fbe05c" stroke-width="1.8"/><path d="M3 6l9 7 9-7M3 18l7-6M21 18l-7-6" fill="none" stroke="#fbe05c" stroke-width="1.5"/></svg>
      </span>
      <span class="icon">
        <svg width="17" height="17" viewBox="0 0 24 24" aria-hidden="true"><circle cx="12" cy="12" r="8.5" fill="#fbe05c"/><path d="M9 6.5c2 1 1 3 3 3.5s1 3-1 3-2 2-1 4M15 14c1 0 2 1 1.5 3" fill="none" stroke="#0b0b0b" stroke-width="1.6"/></svg>
      </span>
      <span class="rule"></span>
    </div>

    <p class="contact contact-line phone">044-555 010 234</p>
    <p class="contact contact-line email">info@vantrotow.com</p>
    <p class="contact contact-line web">www.vantrotow.com</p>
    <div class="divider"></div>
    <p class="contact address">421, Address line goes here<br>45452,Country Name</p>
  </section>
</body>
</html>
```